Design NEW business card

We would like a business card using the colour deep red wine or dark navy blue textured background (patterned or not, open to suggestions) with a high gloss debossed rose gold/copper RM Roland Mercer Jewellery business name (Provided). I have included images for your review we would like to keep our currently logo and business name on the front but you can change the layout and positioning. For the back of the card we are open to all suggestions/variations.
Business
Use our current RM Roland Mercer Jewellery logo (Provided image)

```html
<!DOCTYPE html>
<html lang="en">
<head>
<meta charset="utf-8">
<title>Roland Mercer Jewellery – Business Card</title>
<link href="https://fonts.googleapis.com/css2?family=Montserrat:wght@400;500&display=swap" rel="stylesheet">
<style>
  :root {
    --backdrop: #2b2622;
    --wine: #5c2430;
    --wine-deep: #4f1e28;
    --rose-gold: #c9996f;
    --ink-light: #f3ece8;
  }
  * { margin: 0; padding: 0; box-sizing: border-box; }
  html, body {
    width: 1200px;
    height: 864px;
    overflow: hidden;
    background: var(--backdrop);
    font-family: "Montserrat", sans-serif;
  }
  .stage {
    width: 1200px;
    height: 864px;
    display: flex;
    align-items: center;
    justify-content: center;
    gap: 60px;
  }
  .card {
    width: 525px;
    height: 300px;
    background: linear-gradient(135deg, var(--wine) 0%, var(--wine-deep) 100%);
    border-radius: 3px;
    position: relative;
    box-shadow: 0 10px 30px rgba(0,0,0,0.45);
  }
  /* Front */
  .card-front {
    display: flex;
    align-items: center;
    justify-content: center;
  }
  .brand {
    display: flex;
    align-items: center;
    gap: 14px;
  }
  .brand-dot {
    width: 12px;
    height: 12px;
    border-radius: 50%;
    background: var(--rose-gold);
  }
  .brand-name {
    color: var(--rose-gold);
    font-weight: 500;
    font-size: 20px;
    letter-spacing: 4px;
    text-transform: uppercase;
  }
  /* Back */
  .holder {
    position: absolute;
    right: 34px;
    top: 118px;
    text-align: right;
    font-size: 14px;
    letter-spacing: 0.5px;
    line-height: 1.35;
  }
  .holder-name { color: var(--rose-gold); font-weight: 500; }
  .holder-role { color: var(--ink-light); font-weight: 400; }
  .contact {
    position: absolute;
    left: 34px;
    bottom: 34px;
    font-size: 13px;
    line-height: 1.45;
    color: var(--ink-light);
  }
  .contact .label { color: var(--rose-gold); margin-right: 4px; }
  .contact .web { color: var(--rose-gold); margin-top: 4px; }
</style>
</head>
<body>
  <main class="stage">
    <section class="card card-front" aria-label="Card front">
      <div class="brand">
        <span class="brand-dot"></span>
        <span class="brand-name">Roland Mercer Jewellery</span>
      </div>
    </section>

    <section class="card card-back" aria-label="Card back">
      <div class="holder">
        <div class="holder-name">ADRIAN VOSS</div>
        <div class="holder-role">CEO/FOUNDER</div>
      </div>
      <div class="contact">
        <div>4120 Juniper Court</div>
        <div>Fairbanks, Alaska 99701</div>
        <div><span class="label">P.</span>907 512 4480</div>
        <div><span class="label">E.</span>studio@mercerjewel.com</div>
        <div class="web">www.mercerjewel.com</div>
      </div>
    </section>
  </main>
</body>
</html>
```